Purple Heart Veteran Owned Telecommunications Company

I need to develop my current website (brightwirel.com) into something more upbeat and modern. I created the existing one with SiteKindle and it's very basic. I'm open to using any type of website builder and not just SiteKindle. I feel like SiteKindle is pretty basic. I want something customized to me and my company. I plan on doing a Zorbix Ad, Email Marketing, and Mail Marketing campaign and SEO push. I want a website built so they can look up my company. We are a low voltage telecommunications company based out of Chicago. We are a General Contractor and I have technicians all throughout the US and Canada. I mainly appeal to the government and Summit 500 companies across the country. I focus on commercial and federal work with minor work in Residential. I need to appeal to everyone and not just locally. My company name is Brightwirel. I'm a Marine Corps veteran and my I created the company with my son in mind. We are a service disabled veteran owned small business. I'm open to any play on my logo or color scheme. I do like the color blue but I'm open to anything again. I would like a website that has little maintenance needed and something that is modern and sticks out with my competitors. I'm only in business for 2 years but I need to stick out to my competition so I can start building revenue through ads and getting my name out there with limited funds. I did have a logo and name created which I'm attaching. I'm completely open to changing it if someone can come up with something creative. I would like someone that understands SEO and can help feed work to my site. I'm also open to paying more for the right website that gets everything I want. I know I need to add more pages and more professional. Please use my website as a template but also feel free to come up with any new ideas. I would like some feedback or ideas on what else to add to my website or remove so I can appeal to my audience and look more authentic.

Target Market(s)

Commercial Companies locally in Chicago, and Summit 500 companies and the government

Industry/Entity Type

Telecommunications

Coding

Number of Pages Required

Font styles to use
Sans Serif

Requirements
Must have
• A Modern, fresh look that is customized and original. Something that sticks out to my customers.
Nice to have
• Anything that sticks out and isn't stock. I'm open to anything that is unique and different.
Should not have
• Nothing Generic. I would like something custom tailored to my business

```html
<!DOCTYPE html>
<html lang="en">
<head>
<meta charset="utf-8">
<title>Brightwirel – General Contractor</title>
<link href="https://fonts.googleapis.com/css2?family=Montserrat:wght@600;700&family=Roboto:wght@400;500;700&display=swap" rel="stylesheet">
<style>
:root{
  --navy:#0f3284;
  --navy-deep:#0b2668;
  --ink:#222428;
  --body:#6b6d72;
  --grey-bg:#f1f1f2;
  --slate:#58595b;
  --icon-grey:#6d6e71;
  --footer:#262626;
  --white:#ffffff;
}
*{box-sizing:border-box;margin:0;padding:0}
html,body{width:1200px;height:3843px;overflow:hidden}
body{position:relative;font-family:'Roboto',sans-serif;color:var(--body);background:var(--white)}
.abs{position:absolute}
.heading{font-family:'Montserrat',sans-serif;font-weight:600;letter-spacing:.5px}
.btn{position:absolute;display:flex;align-items:center;justify-content:center;gap:8px;background:var(--navy);color:var(--white);border-radius:24px;font-weight:700;font-size:15px;text-transform:uppercase}
.btn svg{width:15px;height:15px}

/* header */
.brand{left:110px;top:34px;display:flex;align-items:center;gap:10px;color:var(--navy);font-weight:700;font-size:24px;letter-spacing:1px}
.brand .mark{width:18px;height:18px;background:var(--navy)}
.contact-item{top:20px;display:flex;align-items:center;gap:14px}
.contact-item .divider{width:1px;height:34px;background:#c9ccd3}
.contact-item small{display:block;font-size:11px;color:var(--ink);font-weight:500}
.contact-item .val{color:var(--navy);font-weight:500;font-size:15px}
.contact-item .val.big{font-size:20px;font-weight:700}
.nav{top:78px;left:520px;font-size:15px;color:var(--ink);font-weight:500}
.nav span{position:absolute;white-space:nowrap}
.nav .active{color:var(--navy)}
.nav .active:after{content:"";position:absolute;left:-4px;right:-4px;bottom:-10px;height:3px;background:var(--navy)}

/* hero */
.hero{top:110px;left:0;width:1200px;height:708px}
.hero-title{left:112px;top:276px;color:var(--white);font-size:52px}
.hero-tag{left:112px;top:350px;color:var(--white);font-size:17px;line-height:26px;font-weight:500}

/* about */
.about-photo{left:87px;top:896px;width:456px;height:395px;border-radius:6px;background:linear-gradient(135deg,#1d3f8f,#4a6db5 45%,#b98a63 70%,#102a6a)}
.about-title{left:613px;top:908px;font-size:34px;color:#4b4d52}
.about-title b{color:var(--navy);font-weight:700}
.about-text{left:613px;top:973px;width:480px;font-size:14px;line-height:25px}
.about-text p{margin-bottom:10px}

/* services */
.services-bg{left:0;top:1380px;width:1200px;height:650px;background:var(--grey-bg)}
.section-title{left:0;width:1200px;text-align:center;font-size:34px;color:#4b4d52}
.section-title b{color:var(--navy);font-weight:700}
.svc-photo{top:1525px;width:310px;height:191px}
.svc-card{top:1682px;width:286px;height:152px;background:var(--white);border-radius:4px;box-shadow:0 2px 10px rgba(0,0,0,.08);text-align:center;padding-top:24px}
.svc-card h3{font-size:19px;color:var(--ink);font-weight:500;margin-bottom:10px}
.svc-card p{font-size:14px;line-height:24px}

/* pricing */
.pricing{left:0;top:1951px;width:1200px;height:353px}
.pricing-title{left:0;top:2046px;width:1200px;text-align:center;color:var(--white);font-size:33px;font-weight:700}
.pricing-text{left:150px;top:2108px;width:900px;text-align:center;color:var(--white);font-size:14.5px;line-height:26px}

/* sectors */
.sector{width:472px;height:220px;background:var(--white);box-shadow:0 2px 12px rgba(0,0,0,.08);border-right:3px solid var(--navy)}
.sector .photo{position:absolute;left:0;top:0;width:225px;height:220px}
.sector .badge{position:absolute;left:192px;top:79px;width:62px;height:62px;border-radius:50%;background:var(--navy);border:4px solid #dfe4ef;display:flex;align-items:center;justify-content:center}
.sector .badge svg{width:30px;height:30px}
.sector .copy{position:absolute;left:265px;top:42px;width:180px;text-align:center}
.sector h3{font-size:17px;color:var(--ink);font-weight:500;margin-bottom:12px}
.sector p{font-size:14px;line-height:22px}
.sector .more{display:inline-flex;align-items:center;gap:6px;margin-top:12px;color:var(--navy);font-weight:700;font-size:14px}
.sector .more svg{width:14px;height:14px}

/* markets */
.markets{left:0;top:3052px;width:1200px;height:421px}
.market{top:3216px;width:320px;text-align:center;color:var(--white)}
.market .circle{width:82px;height:82px;border-radius:50%;background:var(--icon-grey);margin:0 auto 18px;display:flex;align-items:center;justify-content:center}
.market .circle svg{width:42px;height:42px}
.market h3{font-size:19px;font-weight:700;margin-bottom:8px}
.market p{font-size:14.5px;line-height:21px}

/* footer */
.footer{left:0;top:3473px;width:1200px;height:370px;background:var(--footer)}
.footer-brand{left:127px;top:3640px;color:var(--navy);font-size:28px;font-weight:700;letter-spacing:2px;display:flex;align-items:center;gap:10px}
.footer-brand .mark{width:20px;height:20px;background:var(--navy)}
.social{top:3711px;width:27px;height:27px;border:1.5px solid #cfcfcf;border-radius:50%}
.f-head{top:3549px;color:var(--white);font-size:18px;font-weight:700}
.f-list{color:#e1e1e1;font-size:13.5px}
.f-list div{position:absolute;white-space:nowrap}
.chev{color:#e1e1e1;font-weight:700;margin-right:10px}
.f-ico{position:absolute;width:14px;height:14px}
.copyright{left:0;top:3806px;width:1200px;text-align:center;color:#e1e1e1;font-size:13.5px}
.chat{left:1121px;top:3762px;width:36px;height:36px;border-radius:50%;background:var(--navy);display:flex;align-items:center;justify-content:center}
</style>
</head>
<body>

<div class="abs brand"><span class="mark"></span>BRIGHTWIREL</div>

<div class="abs contact-item" style="left:620px">
  <svg width="28" height="28" viewBox="0 0 24 24" fill="none" stroke="#555" stroke-width="1.4"><rect x="3" y="6" width="18" height="13" rx="1"/><path d="M3 7l9 7 9-7"/></svg>
  <span class="divider"></span>
  <div><small>MAIL US:</small><span class="val">Support@brightwirel.com</span></div>
</div>
<div class="abs contact-item" style="left:900px">
  <svg width="26" height="26" viewBox="0 0 24 24" fill="none" stroke="#555" stroke-width="1.4"><path d="M5 3h4l2 5-3 2a12 12 0 006 6l2-3 5 2v4a2 2 0 01-2 2A17 17 0 013 5a2 2 0 012-2z"/></svg>
  <span class="divider"></span>
  <div><small>CALL US</small><span class="val big">312-555-0148</span></div>
</div>

<nav class="abs nav">
  <span class="active" style="left:0">Home</span>
  <span style="left:73px">Low Voltage</span>
  <span style="left:188px">Our Services</span>
  <span style="left:307px">Markets</span>
  <span style="left:393px">Our Team</span>
  <span style="left:492px">Contact Us</span>
</nav>

<svg class="abs hero" viewBox="0 0 1200 708" role="img" aria-label="Night city skyline with a lit tower reflected over the waterfront">
  <defs>
    <linearGradient id="sky" x1="0" y1="0" x2="0" y2="1">
      <stop offset="0" stop-color="#2447a8"/>
      <stop offset=".5" stop-color="#152f7c"/>
      <stop offset=".75" stop-color="#5a4a56"/>
      <stop offset=".86" stop-color="#b3743e"/>
      <stop offset="1" stop-color="#1a2754"/>
    </linearGradient>
  </defs>
  <polygon points="0,0 1200,0 1200,584 600,668 0,584" fill="url(#sky)"/>
  <polygon points="0,584 600,668 1200,584 1200,598 600,708 0,598" fill="#0f3284"/>
</svg>
<div class="abs heading hero-title">BRIGHTWIREL</div>
<div class="abs hero-tag">We are committed to building trust among our clients,<br>contractors, colleagues, and community</div>
<div class="btn" style="left:112px;top:427px;width:201px;height:46px">Get Started <svg viewBox="0 0 16 16"><circle cx="8" cy="8" r="7" fill="#fff"/><path d="M7 5l3 3-3 3" stroke="#0f3284" stroke-width="2" fill="none"/></svg></div>

<div class="abs about-photo" role="img" aria-label="Close-up of network patch cables and data equipment"></div>
<div class="abs heading about-title">ABOUT <b>US</b></div>
<div class="abs about-text">
  <p>Our past projects include both new construction &amp; repairs/restorations. Occupied and fully operational job sites are never a problem. And we can also plan, manage, and design jobs.</p>
  <p>We offer an end-to-end client experience that includes seamless communication, budgeting, staffing, on-site organization, and solid, quality handiwork every time.</p>
  <p>We are committed to building trust among our clients, contractors, colleagues, and community</p>
</div>
<div class="btn" style="left:613px;top:1225px;width:186px;height:45px">Learn More <svg viewBox="0 0 16 16"><circle cx="8" cy="8" r="7" fill="#fff"/><path d="M7 5l3 3-3 3" stroke="#0f3284" stroke-width="2" fill="none"/></svg></div>

<div class="abs services-bg"></div>
<div class="abs heading section-title" style="top:1438px"><b>OUR</b> SERVICES</div>

<div class="abs svc-photo" style="left:112px;background:linear-gradient(160deg,#1d2430,#3fa7dc 55%,#1a3f6a)" role="img" aria-label="Patch panel with blue network cables"></div>
<div class="abs svc-photo" style="left:445px;background:linear-gradient(90deg,#6b6b6b,#1c1c1c 35%,#2a2a2a 65%,#e3d1b0)" role="img" aria-label="Open server rack cabinet"></div>
<div class="abs svc-photo" style="left:778px;background:linear-gradient(180deg,#dfe3e7,#b9c2c9 50%,#c99a7c 85%,#e8ecef)" role="img" aria-label="Technician mounting a security camera"></div>

<div class="abs svc-card" style="left:124px"><h3>CABILING</h3><p>Low Voltage Wiring and Cabling<br>Voice and Data Network Cabling<br>CAT 3/5/6, Fiber Optic,</p></div>
<div class="abs svc-card" style="left:457px"><h3>NETWORKING</h3><p>Server Racks/Networking Setup<br>Audio/Video Cabling and Wiring<br>WiFi - Wireless Network Installation</p></div>
<div class="abs svc-card" style="left:790px"><h3>INSTALLATION</h3><p>Voice &amp; Telephone Wiring<br>Demarc Extension<br>Security Camera Installation</p></div>

<svg class="abs pricing" viewBox="0 0 1200 353" role="img" aria-label="Dimmed background of a technician at work">
  <polygon points="0,79 600,0 1200,79 1200,353 0,353" fill="#58595b"/>
</svg>
<div class="abs pricing-title">COMPETITIVE PRICING!</div>
<div class="abs pricing-text">Our company has a network of subcontractors nationally and in Canada.&nbsp; We also have the ability to provide our own labor which allows us to offer a competitive edge and provide immediate assistance to our customers.</div>
<div class="btn" style="left:505px;top:2180px;width:190px;height:44px">Learn More <svg viewBox="0 0 16 16"><circle cx="8" cy="8" r="7" fill="#fff"/><path d="M7 5l3 3-3 3" stroke="#0f3284" stroke-width="2" fill="none"/></svg></div>

<div class="abs heading section-title" style="top:2392px"><b>OUR SECTORS</b></div>

<div class="abs sector" style="left:112px;top:2467px">
  <div class="photo" style="background:linear-gradient(180deg,#b9d0e6,#a45b45 45%,#6e5144 80%,#9a9a96)" role="img" aria-label="Brick retail storefront building"></div>
  <div class="badge"><svg viewBox="0 0 24 24" fill="none" stroke="#fff" stroke-width="1.5"><path d="M3 9l2-5h14l2 5H3z"/><path d="M4 9v11h16V9M9 20v-6h6v6"/></svg></div>
  <div class="copy"><h3>Retail</h3><p>Brightwirel has a vast amount of experience as a retail contractor.</p><span class="more">LEARN MORE <svg viewBox="0 0 16 16"><circle cx="8" cy="8" r="6.5" fill="none" stroke="#0f3284" stroke-width="1.6"/><path d="M7 5l3 3-3 3" stroke="#0f3284" stroke-width="1.8" fill="none"/></svg></span></div>
</div>

<div class="abs sector" style="left:615px;top:2467px">
  <div class="photo" style="background:linear-gradient(90deg,#0c1a2e,#3d5a7c 50%,#0c1a2e)" role="img" aria-label="Data center aisle between server racks"></div>
  <div class="badge"><svg viewBox="0 0 24 24" fill="none" stroke="#fff" stroke-width="1.5"><rect x="4" y="4" width="16" height="5"/><rect x="4" y="11" width="16" height="5"/><path d="M12 16v4M7 20h10"/></svg></div>
  <div class="copy"><h3>Data Centers</h3><p>Upper Management has a substantial experience in the telecommunications</p><span class="more">LEARN MORE <svg viewBox="0 0 16 16"><circle cx="8" cy="8" r="6.5" fill="none" stroke="#0f3284" stroke-width="1.6"/><path d="M7 5l3 3-3 3" stroke="#0f3284" stroke-width="1.8" fill="none"/></svg></span></div>
</div>

<div class="abs sector" style="left:112px;top:2725px">
  <div class="photo" style="background:linear-gradient(180deg,#3b6fc4,#6f9ad6 40%,#2a3e66 75%,#c9934f)" role="img" aria-label="Modern hotel building at dusk"></div>
  <div class="badge"><svg viewBox="0 0 24 24" fill="none" stroke="#fff" stroke-width="1.5"><rect x="5" y="3" width="14" height="18"/><path d="M8 7h2M14 7h2M8 11h2M14 11h2M10 21v-5h4v5"/></svg></div>
  <div class="copy"><h3>Hospitality</h3><p>Do you have multiple sites across the country you need completed?</p><span class="more">LEARN MORE <svg viewBox="0 0 16 16"><circle cx="8" cy="8" r="6.5" fill="none" stroke="#0f3284" stroke-width="1.6"/><path d="M7 5l3 3-3 3" stroke="#0f3284" stroke-width="1.8" fill="none"/></svg></span></div>
</div>

<div class="abs sector" style="left:615px;top:2725px">
  <div class="photo" style="background:linear-gradient(180deg,#4a7fd0,#9fbde6 35%,#8a5440 65%,#4d6b3a)" role="img" aria-label="Historic university hall with a central tower"></div>
  <div class="badge"><svg viewBox="0 0 24 24" fill="none" stroke="#fff" stroke-width="1.5"><path d="M2 9l10-5 10 5-10 5z"/><path d="M6 11v5c3 3 9 3 12 0v-5"/></svg></div>
  <div class="copy"><h3>Education</h3><p>Brightwirel is comfortable cabling in the education sector as this field</p><span class="more">LEARN MORE <svg viewBox="0 0 16 16"><circle cx="8" cy="8" r="6.5" fill="none" stroke="#0f3284" stroke-width="1.6"/><path d="M7 5l3 3-3 3" stroke="#0f3284" stroke-width="1.8" fill="none"/></svg></span></div>
</div>

<svg class="abs markets" viewBox="0 0 1200 421" role="img" aria-label="Deep blue band with faint circuit texture">
  <polygon points="0,75 600,0 1200,75 1200,421 0,421" fill="#0f3284"/>
</svg>
<div class="abs heading section-title" style="top:3132px;color:#fff">OUR MARKETS</div>

<div class="abs market" style="left:100px">
  <div class="circle"><svg viewBox="0 0 24 24" fill="none" stroke="#fff" stroke-width="1.3"><path d="M3 9l2-5h14l2 5H3z"/><path d="M4 9v11h16V9M9 20v-6h6v6"/></svg></div>
  <h3>Retail</h3><p>Brightwirel has a vast amount of experience<br>as a retail contractor.</p>
</div>
<div class="abs market" style="left:441px">
  <div class="circle"><svg viewBox="0 0 24 24" fill="none" stroke="#fff" stroke-width="1.3"><rect x="4" y="4" width="11" height="17"/><rect x="15" y="10" width="5" height="11"/><path d="M7 8h2M11 8h1M7 12h2M11 12h1M7 16h2M11 16h1"/></svg></div>
  <h3>Commercial</h3><p>Brightwirel is a leading services provider for<br>Summit 500 businesses with multiple</p>
</div>
<div class="abs market" style="left:782px">
  <div class="circle"><svg viewBox="0 0 24 24" fill="none" stroke="#fff" stroke-width="1.3"><path d="M3 8l9-5 9 5z"/><path d="M5 8v10M9 8v10M15 8v10M19 8v10M3 18h18v2H3z"/></svg></div>
  <h3>Federal</h3><p>We are a trusted provider for the U.S.<br>Government with proven past performance.</p>
</div>

<div class="abs footer"></div>
<div class="abs footer-brand"><span class="mark"></span>BRIGHTWIREL</div>
<div class="abs social" style="left:167px"></div>
<div class="abs social" style="left:202px"></div>
<div class="abs social" style="left:237px"></div>
<div class="abs social" style="left:273px"></div>

<div class="abs f-head" style="left:452px">Quick Links</div>
<div class="abs f-list" style="left:452px;top:0">
  <div style="top:3589px"><span class="chev">»</span>Home</div>
  <div style="top:3622px"><span class="chev">»</span>Low Voltage</div>
  <div style="top:3654px"><span class="chev">»</span>Our Services</div>
  <div style="top:3686px"><span class="chev">»</span>Markets</div>
  <div style="top:3719px"><span class="chev">»</span>Our Team</div>
</div>

<div class="abs f-head" style="left:660px">Important</div>
<div class="abs f-list" style="left:660px;top:0">
  <div style="top:3592px"><span class="chev">»</span>Terms of Use</div>
  <div style="top:3625px"><span class="chev">»</span>Site Map</div>
  <div style="top:3658px"><span class="chev">»</span>Privacy Policy</div>
  <div style="top:3690px"><span class="chev">»</span>Disclaimer</div>
</div>

<div class="abs f-head" style="left:863px">Contact us</div>
<div class="abs f-list" style="left:863px;top:0">
  <svg class="f-ico" style="top:3600px" viewBox="0 0 24 24" fill="#e1e1e1"><path d="M12 2a7 7 0 00-7 7c0 5 7 13 7 13s7-8 7-13a7 7 0 00-7-7zm0 9.5A2.5 2.5 0 1112 6a2.5 2.5 0 010 5.5z"/></svg>
  <div style="left:31px;top:3599px;line-height:22px">123, Lorem ipsum dolor sit amet,<br>consectetur elit,</div>
  <svg class="f-ico" style="top:3655px" viewBox="0 0 24 24" fill="#e1e1e1"><rect x="6" y="2" width="12" height="20" rx="2"/><rect x="8" y="5" width="8" height="12" fill="#262626"/></svg>
  <div style="left:31px;top:3655px">+555-555-5555</div>
  <svg class="f-ico" style="top:3690px" viewBox="0 0 24 24" fill="#e1e1e1"><rect x="3" y="8" width="18" height="12" rx="1"/><rect x="7" y="3" width="10" height="6"/></svg>
  <div style="left:31px;top:3689px">+ 123 456 7892</div>
  <svg class="f-ico" style="top:3724px" viewBox="0 0 24 24" fill="none" stroke="#e1e1e1" stroke-width="2"><rect x="3" y="6" width="18" height="13"/><path d="M3 7l9 6 9-6"/></svg>
  <div style="left:31px;top:3723px">info@brightwirel.com</div>
</div>

<div class="abs copyright">© 2021&nbsp; brightwirel&nbsp; |&nbsp; All Rights Reserved</div>
<div class="abs chat"><svg width="18" height="18" viewBox="0 0 24 24" fill="#fff"><path d="M12 3C6.5 3 2 6.8 2 11.5c0 2.4 1.2 4.6 3.1 6.1L4 21l4.2-2c1.2.4 2.5.6 3.8.6 5.5 0 10-3.8 10-8.5S17.5 3 12 3z"/></svg></div>

</body>
</html>
```